Business Card Design for Online Gift Business

Business card design for a new online Canadian company called "Harlow & Brine Gift Boxes" selling modern and luxurious gift boxes for every occasion. Items are sourced locally from talented socially-responsible Canadian artisans. Each gift is elegantly presented in a keepsake wood box to ensure a lasting impression.

Industry/Entity Type

E-Commerce

Contact Information for Business Card

Marla Whitcombe, Proprietor
Calgary, AB
403-555-2741
www.harlowandbrine.ca
hello@harlowandbrine.ca

Requirements
Must have
• Gifts from our best, to your best
• Please also include the symbols for Facebook and Instagram
Nice to have
• **I have attached a few samples of background colors and font colors that I like. I hope this helps in a few directions to try.

```html
<!DOCTYPE html>
<html lang="en">
<head>
<meta charset="utf-8">
<title>Harlow &amp; Brine Gift Boxes — Business Card</title>
<link href="https://fonts.googleapis.com/css2?family=PT+Sans:wght@400;700&display=swap" rel="stylesheet">
<style>
  :root {
    --backdrop: #5b4a3b;
    --card-front: #cfc4b2;
    --card-back: #ffffff;
    --tan: #b09a74;
    --tan-light: #bfab88;
    --ink: #6b4a33;
    --ink-soft: #7a5a42;
    --edge: #4a3a2c;
  }
  * { margin: 0; padding: 0; box-sizing: border-box; }
  html, body { width: 1200px; height: 987px; overflow: hidden; }
  body {
    background: var(--backdrop);
    font-family: "PT Sans", sans-serif;
    position: relative;
  }
  .card {
    position: absolute;
    left: 293px;
    width: 615px;
    height: 351px;
    overflow: hidden;
  }
  .card--front { top: 124px; background: var(--card-front); }
  .card--back { top: 511px; background: var(--card-back); }

  .wordmark {
    position: absolute;
    left: 40px;
    top: 62px;
    font-size: 34px;
    font-weight: 400;
    color: var(--ink);
    letter-spacing: 0.5px;
    white-space: nowrap;
  }
  .edge-tab {
    position: absolute;
    left: -3px;
    top: 165px;
    width: 15px;
    height: 42px;
    background: var(--tan);
    border-right: 3px solid var(--edge);
  }
  .contact {
    position: absolute;
    left: 43px;
    top: 165px;
    color: var(--ink);
  }
  .contact__name { font-size: 21px; font-weight: 700; line-height: 1.2; }
  .contact__role { font-size: 16px; line-height: 1.3; color: var(--ink-soft); margin-left: 2px; }
  .contact__city { font-size: 15px; line-height: 1.3; color: var(--ink-soft); margin-top: 12px; }
  .contact__line {
    display: flex;
    align-items: center;
    gap: 8px;
    font-size: 15px;
    line-height: 1.3;
    color: var(--ink-soft);
    margin-top: 6px;
    white-space: nowrap;
  }
  .contact__line svg { width: 14px; height: 14px; flex: none; }

  .emblem {
    position: absolute;
    left: 316px;
    top: 16px;
    width: 282px;
    height: 335px;
    background: linear-gradient(180deg, var(--tan-light), var(--tan));
    box-shadow: 4px 4px 0 var(--edge);
  }

  .wordmark--back {
    left: 0;
    right: 0;
    top: 128px;
    text-align: center;
    font-size: 40px;
    color: var(--tan-light);
  }
  .tagline {
    position: absolute;
    left: 0;
    right: 0;
    top: 190px;
    text-align: center;
    font-size: 16px;
    font-style: normal;
    color: var(--ink-soft);
    letter-spacing: 1px;
  }
  .social {
    position: absolute;
    left: 0;
    right: 0;
    top: 240px;
    display: flex;
    justify-content: center;
    gap: 28px;
    font-size: 14px;
    color: var(--ink-soft);
  }
  .social__item { display: flex; align-items: center; gap: 7px; }
  .social__dot {
    width: 14px;
    height: 14px;
    border-radius: 50%;
    background: var(--tan);
  }
  .social__square {
    width: 14px;
    height: 14px;
    background: var(--tan);
  }
</style>
</head>
<body>
  <section class="card card--front">
    <div class="wordmark">Harlow &amp; Brine</div>
    <div class="edge-tab"></div>
    <div class="contact">
      <p class="contact__name">Marla Whitcombe</p>
      <p class="contact__role">Proprietor</p>
      <p class="contact__city">Calgary, AB</p>
      <p class="contact__line">
        <svg viewBox="0 0 24 24" aria-hidden="true"><path fill="#6b4a33" d="M6.6 10.8a15.1 15.1 0 0 0 6.6 6.6l2.2-2.2c.3-.3.7-.4 1-.2 1.1.4 2.3.6 3.6.6.6 0 1 .4 1 1V20c0 .6-.4 1-1 1A17 17 0 0 1 3 4c0-.6.4-1 1-1h3.5c.6 0 1 .4 1 1 0 1.3.2 2.5.6 3.6.1.3 0 .7-.2 1z"/></svg>
        403-555-2741
      </p>
      <p class="contact__line">
        <svg viewBox="0 0 24 24" aria-hidden="true"><circle cx="12" cy="12" r="10" fill="#6b4a33"/><path fill="none" stroke="#cfc4b2" stroke-width="1.6" d="M2 12h20M12 2c3 3 3 17 0 20M12 2c-3 3-3 17 0 20"/></svg>
        www.harlowandbrine.ca
      </p>
      <p class="contact__line">
        <svg viewBox="0 0 24 24" aria-hidden="true"><rect x="2" y="5" width="20" height="14" rx="2" fill="#6b4a33"/><path fill="none" stroke="#cfc4b2" stroke-width="1.6" d="M3 6l9 7 9-7"/></svg>
        hello@harlowandbrine.ca
      </p>
    </div>
    <div class="emblem" role="img" aria-label="Large decorative emblem in tan"></div>
  </section>

  <section class="card card--back">
    <div class="wordmark wordmark--back">Harlow &amp; Brine</div>
    <p class="tagline">Gifts from our best, to your best</p>
    <div class="social">
      <span class="social__item"><span class="social__dot"></span>/harlowandbrine</span>
      <span class="social__item"><span class="social__square"></span>@harlowandbrine</span>
    </div>
  </section>
</body>
</html>
```